The Vantor Codex Book Cover

"The Vantor Codex" is a book I wrote with the slogan "Unlock Performance, Spark Engagement: Master the Art of Building Winning Cultures in Today's Hybrid World". The book is designed around a methodology that's mine and that I attached. I would love to see the graphic of the methodology integrated in the design in a very subtle way. Use colors from the model but the book cover should be catchy, modern and engaging to the eye.
Overall the book is about three key elements towards success:
- (Self) Directions (purpose)
- Human experience (people and psychological safety)
- Maximize engagement
The methodology is a FLOW so flow is something that could be incorporated as well in the concept.
Low design quality
Managers and Teams

```html
<!DOCTYPE html>
<html lang="en">
<head>
<meta charset="UTF-8">
<title>The Vantor Codex — Book Cover</title>
<link rel="stylesheet" href="https://fonts.googleapis.com/css2?family=Cinzel:wght@600;700&family=Crimson+Pro:wght@400;700&display=swap">
<style>
  :root {
    --stage: #c9ced3;
    --paper: #ffffff;
    --brand-blue: #2ea8df;
    --band-blue: #29a5dc;
    --ink-gray: #58595b;
    --rule-gray: #6d6e70;
    --ink-dark: #1e1e1e;
    --gear-pink: #e0457b;
    --gear-teal: #1f7f9b;
    --gear-green: #22b48f;
    --gear-orange: #f26b1d;
    --gear-yellow: #f2b705;
  }
  * { margin: 0; padding: 0; box-sizing: border-box; }
  html, body { width: 1200px; height: 1200px; overflow: hidden; }
  body {
    background: linear-gradient(180deg, #b7bec5 0%, var(--stage) 55%, #d9dde1 100%);
    position: relative;
  }
  .cover {
    position: absolute;
    left: 283px;
    top: 50px;
    width: 634px;
    height: 1100px;
    background: var(--paper);
    overflow: hidden;
  }
  .title-the {
    position: absolute;
    top: 52px;
    left: 0;
    width: 100%;
    display: flex;
    align-items: center;
    justify-content: center;
    gap: 22px;
    padding: 0 58px;
  }
  .title-the .rule {
    flex: 1;
    height: 4px;
    background: var(--rule-gray);
  }
  .title-the .word {
    font-family: "Cinzel", serif;
    font-weight: 700;
    font-size: 74px;
    line-height: 1;
    color: var(--ink-gray);
  }
  .title-main {
    position: absolute;
    top: 132px;
    left: 0;
    width: 100%;
    text-align: center;
    font-family: "Cinzel", serif;
    font-weight: 700;
    font-size: 112px;
    line-height: 1;
    color: var(--brand-blue);
  }
  .title-sub {
    position: absolute;
    top: 258px;
    left: 0;
    width: 100%;
    text-align: center;
    font-family: "Cinzel", serif;
    font-weight: 700;
    font-size: 112px;
    line-height: 1;
    color: var(--ink-gray);
  }
  .tagline {
    position: absolute;
    top: 394px;
    left: 100px;
    width: 434px;
    padding: 12px 0;
    border-top: 1.5px solid var(--ink-dark);
    border-bottom: 1.5px solid var(--ink-dark);
    text-align: center;
    font-family: "Crimson Pro", serif;
    font-weight: 700;
    font-size: 25px;
    line-height: 1;
    color: var(--ink-dark);
  }
  .flow-artwork {
    position: absolute;
    top: 490px;
    left: 62px;
    width: 510px;
    height: 270px;
    border-radius: 24px;
    background: linear-gradient(100deg,
      var(--gear-pink) 0%,
      var(--gear-teal) 25%,
      var(--gear-green) 50%,
      var(--gear-orange) 75%,
      var(--gear-yellow) 100%);
    opacity: 0.85;
  }
  .promise {
    position: absolute;
    top: 815px;
    left: 0;
    width: 100%;
    text-align: center;
    font-family: "Crimson Pro", serif;
    font-weight: 400;
    font-size: 25px;
    line-height: 1.3;
    color: var(--ink-dark);
  }
  .author-band {
    position: absolute;
    left: 0;
    bottom: 0;
    width: 100%;
    height: 166px;
    background: var(--band-blue);
    display: flex;
    align-items: flex-start;
    justify-content: center;
    padding-top: 34px;
  }
  .author-name {
    font-family: "Cinzel", serif;
    font-weight: 600;
    font-size: 56px;
    line-height: 1;
    letter-spacing: 3px;
    color: var(--paper);
  }
</style>
</head>
<body>
  <main class="cover">
    <div class="title-the">
      <span class="rule"></span>
      <span class="word">THE</span>
      <span class="rule"></span>
    </div>
    <h1 class="title-main">VANTOR</h1>
    <div class="title-sub">CODEX</div>
    <p class="tagline">Unlock Performance, Spark Engagement</p>
    <div class="flow-artwork" role="img" aria-label="Colourful interlocking gears in pink, teal, green, orange and yellow with team members working around them, seen from above"></div>
    <p class="promise">Master the Art of Building Winning Cultures<br>in Today's Hybrid World</p>
    <footer class="author-band">
      <span class="author-name">LARS VENDRIK</span>
    </footer>
  </main>
</body>
</html>
```